Storm Restoration Contractor needs a professional letterhead design

Looking for a professional letterhead design. Not looking for your cheapo MS Word standard ones that are readily available. Dont want it to be cookie cutter look like ones readily available online. We just recently changed our logo and want to freshen up all our documents. Our company handles restoring a property back to a pre-loss condition after a storm damages it. For example, wind, hail, flood, fire losses.

Target Market(s)

Property Owners, Homeowners, Property Owners, Commercial Property Owners, Property Management Companies

Industry/Entity Type

Construction Company

Requirements
Must have
• Professional, Use 1 of 2 logo options
• Storm Restoration, Roofing, Siding, Windows

```html
<!DOCTYPE html>
<html lang="en">
<head>
<meta charset="utf-8">
<title>Northgate Exteriors Letterhead</title>
<link href="https://fonts.googleapis.com/css2?family=Didact+Gothic&display=swap" rel="stylesheet">
<style>
  :root {
    --backdrop: #d6d6d6;
    --paper: #f1f1f1;
    --ink: #1e1e1e;
    --ink-soft: #3a3a3a;
    --brand-blue: #1f64b4;
    --brand-gray: #4f4f4f;
    --signature-tone: #d3dbee;
  }
  * { margin: 0; padding: 0; box-sizing: border-box; }
  html, body {
    width: 1200px; height: 1041px; overflow: hidden;
    background: var(--backdrop);
    font-family: "Didact Gothic", "Century Gothic", sans-serif;
    color: var(--ink);
  }
  .letterhead {
    position: absolute; left: 197px; top: 0;
    width: 806px; height: 1041px;
    background: var(--paper);
  }
  .brand {
    position: absolute; left: 66px; top: 61px;
    display: flex; align-items: center; gap: 10px;
  }
  .brand-dot {
    width: 58px; height: 58px; border-radius: 50%;
    background: var(--brand-blue);
  }
  .brand-name {
    font-size: 27px; line-height: 27px; color: var(--brand-blue);
    letter-spacing: 1px; text-transform: uppercase;
  }
  .contact {
    position: absolute; left: 579px; top: 58px;
    font-style: normal;
    font-size: 10.5px; line-height: 14px; color: var(--ink-soft);
  }
  .contact-address {
    border-left: 2px solid var(--brand-blue); padding-left: 11px;
  }
  .contact-lines {
    margin-top: 10px; border-left: 1px solid var(--brand-gray); padding-left: 12px;
  }
  .contact-lines li { list-style: none; display: flex; align-items: center; gap: 6px; }
  .contact-lines svg { width: 10px; height: 10px; fill: var(--brand-blue); }
  .letter {
    position: absolute; left: 66px; top: 228px; width: 670px;
    font-size: 11.3px; line-height: 14.1px;
  }
  .date { margin-bottom: 14px; }
  .recipient { margin-bottom: 64px; }
  .salutation { font-weight: bold; margin-bottom: 14px; letter-spacing: .2px; }
  .letter p.body { text-align: justify; margin-bottom: 14px; }
  .closing { position: relative; margin-top: 28px; }
  .closing strong { display: block; }
  .signature {
    position: absolute; left: 92px; top: -12px;
    width: 160px; height: 60px; border-radius: 30px;
    background: var(--signature-tone);
  }
  .footer-rule {
    position: absolute; left: 0; bottom: 0; width: 806px; height: 14px;
    background: var(--brand-gray);
    border-top: 4px solid var(--brand-blue);
  }
</style>
</head>
<body>
  <main class="letterhead">
    <header>
      <div class="brand">
        <span class="brand-dot"></span>
        <span class="brand-name">Northgate<br>Exteriors</span>
      </div>
      <address class="contact">
        <div class="contact-address">4120 W Ridgeline Road STE 210<br>Mesa, AZ 85201</div>
        <ul class="contact-lines">
          <li><svg viewBox="0 0 10 10"><path d="M2 0l2 2-1 1.5c.6 1.4 1.6 2.4 3 3L7.5 5.5l2 2L8 10C4 9.5.5 6 0 2z"/></svg>480-555-0142</li>
          <li><svg viewBox="0 0 10 10"><rect x="2" y="0" width="6" height="3"/><rect x="0" y="4" width="10" height="4"/><rect x="2" y="7" width="6" height="3"/></svg>480-555-0142</li>
          <li><svg viewBox="0 0 10 10"><path d="M0 2h10v6H0z"/></svg>info@northgateext.com</li>
        </ul>
      </address>
    </header>

    <section class="letter">
      <div class="date">30.11.2016</div>
      <div class="recipient">Recipient's name<br>Lindenweg 12<br>10115 Berlin<br>Germany</div>
      <div class="salutation">Dear sir,</div>
      <p class="body">Communication is a very integral part of living creatures, animals and humans. Communication may be verbal or written. Written communication however is only applicable to human beings. Can you even imagine a world without communication? Verbal communication can be through telephones, webcams or in person. Written communication is through letters, emails and mobile phone messages.</p>
      <p class="body">In today's world of great inventions and technology, letters have somehow become redundant. It is the time for text messages or chats. But they still can communicate a lot more than all other modes of communication. Organizations and various government departments still bank on letters as a strong medium of communication. There is no comparison in costs of sending letters as compared to costs of mobile phone messages though – letters are far cheaper. Letters now commonly known as “hard copy documents” are considered more relevant and important than email copies of text messages as proof or evidence of some sort.</p>
      <p class="body">Letters speak volumes about a person or an organization that writes it. So one must take utmost care ensuring that the language used in any letter is appropriate for the occasion for which it is being written. Since a letter is also a written proof or document, if there are certain things that should not form a part of it, then that too should be carefully handled.</p>
      <p class="body">Writing a good letter is an art. But if for some reason someone is unable to write that perfect letter, these different types of letters provide a base for you to build on. Sample letters have been given for everyone to understand what all information needs to form a part of the letter type and then it can be customized.</p>
      <div class="closing">
        Yours Sincerely,
        <strong>Lena Corvin</strong>
        <div class="signature" role="img" aria-label="Handwritten signature of Lena Corvin"></div>
      </div>
    </section>

    <div class="footer-rule" aria-hidden="true"></div>
  </main>
</body>
</html>
```